Exciting & Elegant Stationary Pack

Stationary consists of
1. Letter head / Envelope
2. Business Card
3. Invoice
4. 40x40mm sticker

Attached files;

1. Logo (Other formats available on request)
2. MS word Doc - For information and description of design
3. Website image (This will be our new website so use the colours so everything ties together)
4. Sample of stationary pack we like, but feel free to be creative

Target Market(s)

Home improvement

Industry/Entity Type

Construction

Font styles to use
Other font styles liked:
• Leave up to designer - We like font used on (website attached image)

Requirements
Must have
• Please look at uploaded file of sample website and use colours
Nice to have
• Any type of business card design - eg. metal, die cut, embossed, etc...

```html
<!DOCTYPE html>
<html lang="en">
<head>
<meta charset="utf-8">
<title>Grout &amp; Tile Co — Business Card</title>
<link rel="stylesheet" href="https://fonts.googleapis.com/css2?family=Montserrat:wght@400;800&family=Open+Sans:wght@400&display=swap">
<style>
  :root {
    --navy: #124a70;
    --band: #9dc3e6;
    --orange: #f39a4a;
    --paper: #ffffff;
    --ink: #2f3d4a;
    --backdrop: #e9e6e1;
  }
  html, body {
    margin: 0;
    padding: 0;
    width: 1200px;
    height: 950px;
    overflow: hidden;
    background: var(--backdrop);
  }
  .canvas {
    position: relative;
    width: 1200px;
    height: 950px;
  }
  .card {
    position: absolute;
    background: var(--paper);
    box-shadow: 0 10px 28px rgba(0,0,0,0.18);
    overflow: hidden;
  }
  .card-front {
    left: 80px;
    top: 90px;
    width: 640px;
    height: 366px;
  }
  .card-back {
    left: 500px;
    top: 500px;
    width: 620px;
    height: 354px;
    display: flex;
    align-items: center;
    justify-content: center;
  }
  .band {
    position: absolute;
    inset: 0;
  }
  .identity {
    position: absolute;
    left: 44px;
    top: 42px;
  }
  .person-name {
    margin: 0;
    font-family: "Montserrat", sans-serif;
    font-weight: 800;
    font-size: 40px;
    letter-spacing: 0.5px;
    color: var(--navy);
    line-height: 1;
  }
  .person-role {
    margin: 6px 0 0;
    font-family: "Montserrat", sans-serif;
    font-weight: 400;
    font-size: 27px;
    letter-spacing: 0.5px;
    color: var(--orange);
    line-height: 1.1;
  }
  .contact {
    position: absolute;
    top: 220px;
    width: 200px;
    display: flex;
    flex-direction: column;
    align-items: center;
    font-family: "Open Sans", sans-serif;
    font-size: 15px;
    color: var(--ink);
  }
  .contact-phone { left: 10px; }
  .contact-email { left: 230px; }
  .contact-web { left: 430px; }
  .contact-text { margin-top: 14px; white-space: nowrap; }
  .licence {
    position: absolute;
    left: 230px;
    top: 190px;
    width: 200px;
    text-align: center;
    font-family: "Open Sans", sans-serif;
    font-size: 14px;
    color: var(--ink);
  }
  .hex-icon { width: 46px; height: 50px; display: block; }
  .brand {
    display: flex;
    align-items: center;
    gap: 16px;
  }
  .brand-square {
    width: 34px;
    height: 34px;
    background: var(--navy);
  }
  .brand-name {
    font-family: "Montserrat", sans-serif;
    font-weight: 800;
    font-size: 42px;
    color: var(--navy);
    letter-spacing: 0.5px;
  }
</style>
</head>
<body>
<main class="canvas">

  <section class="card card-front" aria-label="Business card front">
    <svg class="band" viewBox="0 0 640 366" preserveAspectRatio="none" aria-hidden="true">
      <path d="M0 172 H250 C285 172 290 134 330 134 C370 134 375 172 410 172 H640 V366 H0 Z" fill="var(--band)"/>
    </svg>

    <div class="identity">
      <h1 class="person-name">LINH TRAN</h1>
      <p class="person-role">PROJECT MANAGER</p>
    </div>

    <p class="licence">Lic No. 204618c</p>

    <div class="contact contact-phone">
      <svg class="hex-icon" viewBox="0 0 46 50" aria-hidden="true">
        <polygon points="23,0 46,12.5 46,37.5 23,50 0,37.5 0,12.5" fill="var(--navy)"/>
        <rect x="16" y="14" width="14" height="22" rx="2" fill="none" stroke="#fff" stroke-width="2"/>
        <circle cx="23" cy="32" r="1.4" fill="#fff"/>
      </svg>
      <span class="contact-text">0400 555 017</span>
    </div>

    <div class="contact contact-email">
      <svg class="hex-icon" viewBox="0 0 46 50" aria-hidden="true">
        <polygon points="23,0 46,12.5 46,37.5 23,50 0,37.5 0,12.5" fill="var(--navy)"/>
        <rect x="12" y="17" width="22" height="16" fill="#fff"/>
        <polyline points="12,17 23,26 34,17" fill="none" stroke="var(--navy)" stroke-width="1.6"/>
      </svg>
      <span class="contact-text">info@groutandtile.com.au</span>
    </div>

    <div class="contact contact-web">
      <svg class="hex-icon" viewBox="0 0 46 50" aria-hidden="true">
        <polygon points="23,0 46,12.5 46,37.5 23,50 0,37.5 0,12.5" fill="var(--navy)"/>
        <circle cx="23" cy="25" r="10" fill="none" stroke="#fff" stroke-width="2"/>
        <ellipse cx="23" cy="25" rx="4.5" ry="10" fill="none" stroke="#fff" stroke-width="1.5"/>
        <line x1="13" y1="25" x2="33" y2="25" stroke="#fff" stroke-width="1.5"/>
      </svg>
      <span class="contact-text">groutandtile.com.au</span>
    </div>
  </section>

  <section class="card card-back" aria-label="Business card back">
    <div class="brand">
      <span class="brand-square" aria-hidden="true"></span>
      <span class="brand-name">Grout &amp; Tile Co</span>
    </div>
  </section>

</main>
</body>
</html>
```